Cutting Edge Property Services Provider is Looking to Update Business Card Design

We are looking to freshen up our business cards to match our cutting edge technology based image.

KORVANEX - Where Care Finds Its Pulse

More information about our company can be found on our website at www.korvanex-demo.net

We integrate technology in a historically low tech industry.

We have appeared on the Brisk 300/3000 list 2 years in a row and we're previously recognized as the 5th Quickest Rising Firm in San Diego.

Our core colors are blue and white, but are not against accents that might improve our image.

We currently have our Mission Statement on our Business Cards in a folding design:
KORVANEX IS THE LEADING BUILDING SERVICES INNOVATOR. BY COMBINING TECHNOLOGY WITH FUNCTIONAL TOOS THAT IMPROVE EFFICIENCY IN THE WORKPLACE, WE PROVIDE UNPARALLELED SERVICE IN THE INDUSTRY. DEVELOPING LASTING RELATIONSHIPS WITH OUR CLIENTS AND ASSOCIATES IS THE CORNERSTONE OF OUR SUCCESS.

We'd like to convey the image of a cutting edge, technology based company. Want the cards to pop.

Target Market(s)

Commercial Property Managers - 20 to 50 year old professionals

Industry/Entity Type

Business

Requirements
Must have
• Must utilize our logo obviously, but are definitely open to using variations on the logo. Utilizing the components of the logo, but maybe in different configurations or backgrounds, etc...

Must use the Name: KORVANEX.
Can also use KORVANEX PROPERTY SERVICES.

Must include the Mission Statement

Must say: Where Care Finds Its Pulse
Nice to have
• We are considering plastic stock, shaped cards, or folding cards.

Nothing over the top or really expensive, but will consider if it conveys innovation and technology.
Should not have
• No images of toilets, buildings, trees, or anything relating to commercial properties.

We want to convey our technology image.

```html
<!DOCTYPE html>
<html lang="en">
<head>
<meta charset="utf-8">
<title>Korvanex Business Card</title>
<link href="https://fonts.googleapis.com/css2?family=Jost:wght@400;500;700&display=swap" rel="stylesheet">
<style>
  :root {
    --brand-blue: #0e4c7c;
    --ink: #1f2a33;
    --card: #ffffff;
    --stage: #8a5a3a;
    --band-grey: #5d6064;
    --label: #111111;
  }
  * { margin: 0; padding: 0; box-sizing: border-box; }
  html, body { width: 1200px; height: 713px; overflow: hidden; }
  body {
    background: var(--stage);
    font-family: "Jost", "Futura", sans-serif;
    position: relative;
  }
  .side-label {
    position: absolute; top: 30px; width: 200px; text-align: center;
    font-size: 22px; color: var(--label);
  }
  .side-label--front { left: 222px; }
  .side-label--back { left: 803px; }

  .card {
    position: absolute; width: 525px; height: 298px;
    background: var(--card); border-radius: 22px; overflow: hidden;
    box-shadow: 0 4px 10px rgba(0,0,0,.35);
  }
  .card--front-top { left: 55px; top: 72px; }
  .card--front-bottom { left: 55px; top: 372px; }
  .card--back-top { left: 640px; top: 72px; }
  .card--back-bottom { left: 640px; top: 372px; }

  .brand { position: absolute; display: flex; flex-direction: column; align-items: center; }
  .brand__square { background: var(--brand-blue); }
  .brand__name {
    font-weight: 700; color: var(--brand-blue); letter-spacing: 2px; line-height: 1;
  }

  .card--front-top .brand { left: 0; right: 0; top: 55px; }
  .card--front-top .brand__square { width: 150px; height: 150px; }
  .card--front-top .brand__name { font-size: 44px; margin-top: 22px; }

  .card--back-top .brand { left: 0; right: 0; top: 48px; }
  .card--back-top .brand__square { width: 100px; height: 100px; }
  .card--back-top .brand__name { font-size: 26px; margin-top: 12px; }
  .tagline {
    position: absolute; left: 0; right: 0; top: 246px; text-align: center;
    font-size: 18px; color: var(--brand-blue);
  }

  .mission {
    position: absolute; left: 40px; right: 40px; top: 82px;
    text-align: center; font-size: 17px; line-height: 22px; color: var(--ink);
  }

  .card--back-bottom .brand { left: 25px; width: 200px; top: 52px; }
  .card--back-bottom .brand__square { width: 100px; height: 100px; }
  .card--back-bottom .brand__name { font-size: 24px; margin-top: 14px; }

  .contact { position: absolute; left: 300px; top: 50px; color: var(--ink); }
  .contact__name { font-size: 21px; color: var(--brand-blue); line-height: 24px; }
  .contact__role { font-size: 15px; color: var(--brand-blue); margin-bottom: 6px; }
  .contact__line { font-size: 14px; line-height: 22px; }
  .contact__line b { font-weight: 700; }
  .contact__address { font-size: 13px; line-height: 18px; margin-top: 8px; }

  .footer-band { position: absolute; left: 0; bottom: 0; width: 525px; height: 55px; }
  .footer-web {
    position: absolute; left: 300px; bottom: 12px; color: #fff;
    font-size: 13px; line-height: 18px;
  }
  .footer-web b { font-weight: 700; }
</style>
</head>
<body>
  <div class="side-label side-label--front">Front</div>
  <div class="side-label side-label--back">Back</div>

  <section class="card card--front-top">
    <div class="brand">
      <div class="brand__square"></div>
      <div class="brand__name">KORVANEX</div>
    </div>
  </section>

  <section class="card card--front-bottom">
    <p class="mission">Korvanex is the leading building services innovator. By combining technology with functional toos that improve efficiency in the workplace, we provide unparalleled service in the industry. Developing lasting relationships with our clients and associates is the cornerstone of our success.</p>
  </section>

  <section class="card card--back-top">
    <div class="brand">
      <div class="brand__square"></div>
      <div class="brand__name">KORVANEX</div>
    </div>
    <p class="tagline">Where Care Finds Its Pulse</p>
  </section>

  <section class="card card--back-bottom">
    <div class="brand">
      <div class="brand__square"></div>
      <div class="brand__name">KORVANEX</div>
    </div>
    <div class="contact">
      <div class="contact__name">Your Name</div>
      <div class="contact__role">Designation</div>
      <div class="contact__line"><b>c</b> : +12 345 67 8910</div>
      <div class="contact__line"><b>p</b> : +12 345 67 8910</div>
      <div class="contact__address">123, Abc Street<br>0000 City, Country</div>
    </div>
    <svg class="footer-band" viewBox="0 0 525 55" aria-hidden="true">
      <polygon points="0,26 250,26 238,40 0,40" fill="var(--band-grey)"/>
      <polygon points="290,0 525,0 525,55 240,55" fill="var(--brand-blue)"/>
    </svg>
    <div class="footer-web"><b>w</b> : www.korvanex-demo.net<br><b>e</b> : info@korvanex-demo.net</div>
  </section>
</body>
</html>
```